Catering Menu Package

I currently have a complete menu package, which we have redesigned as far as content, now I need to it put together in a catalog type format. It is essentially 10-12 pages in length, and will be sent for print production. Upon receiving a final edit
Updates

I have added an example gif to the project.

I did this free hand this basically what I am looking for. please change text and type to whatever you think would look best. This is a total rough design so, feel free to change any and everything. The text for the page is on the word documents. If you need more images let me know I am in the process of getting as many images uploaded for your use.

Project Deadline Extended
Reason: I figured we got a late jump with questions, so i am extending a few days .

Target Market(s)

The target market is business who wish to have catered luncheons, breakfasts , meetings

Industry/Entity Type

Catering

Requirements
Must have
• I have attached a copy of the text that what we want in the package, our logo, and i have also attached a catering package of another company to give you an idea what the finished product will be
Should not have
• It should not look identical to the example catering packages, these are for some inspiration we want our own design with the same type of look and feel

```html
<!DOCTYPE html>
<html lang="en">
<head>
<meta charset="utf-8">
<title>Sandwich Combos and Add Ons</title>
<link href="https://fonts.googleapis.com/css2?family=Great+Vibes&family=Alegreya:wght@400&display=swap" rel="stylesheet">
<style>
  :root {
    --paper: #ebe5d8;
    --paper-soft: #e3dccc;
    --ink: #1d1a17;
    --photo-dark: #3a2e22;
    --photo-mid: #8a7a5c;
    --photo-light: #d9cdb2;
    --citrus: #e6a43c;
    --brand: #ffffff;
  }
  * { margin: 0; padding: 0; box-sizing: border-box; }
  html, body { width: 1200px; height: 928px; overflow: hidden; background: #ffffff; }
  .menu-page {
    position: relative;
    width: 1200px;
    height: 928px;
    overflow: hidden;
  }
  .menu-panel {
    position: absolute;
    left: 0; top: 0;
    width: 582px; height: 928px;
    background: radial-gradient(ellipse at 40% 45%, var(--paper) 0%, var(--paper-soft) 100%);
    color: var(--ink);
    font-family: "Alegreya", Georgia, serif;
  }
  .section-title {
    position: absolute;
    left: 120px;
    font-family: "Great Vibes", cursive;
    font-weight: 400;
    font-size: 44px;
    line-height: 1;
    letter-spacing: 0.5px;
  }
  .combos-title { top: 150px; }
  .addons-title { top: 404px; }
  .item-list {
    position: absolute;
    left: 122px;
    list-style: none;
    font-size: 17px;
  }
  .combo-list { top: 213px; line-height: 21.6px; }
  .addon-list { top: 468px; line-height: 21.2px; }
  .food-photo {
    position: absolute;
    left: 582px; top: 0;
    width: 618px; height: 928px;
    background:
      radial-gradient(circle at 68% 78%, var(--citrus) 0%, rgba(230,164,60,0) 22%),
      radial-gradient(ellipse at 45% 35%, var(--photo-light) 0%, var(--photo-mid) 40%, var(--photo-dark) 85%);
  }
  .brand-mark {
    position: absolute;
    left: 1068px; top: 740px;
    width: 96px;
    display: flex;
    flex-direction: column;
    align-items: center;
    gap: 8px;
    color: var(--brand);
    font-family: "Alegreya", Georgia, serif;
    font-size: 15px;
    line-height: 1.05;
    text-align: center;
  }
  .brand-dot {
    width: 64px; height: 64px;
    border-radius: 50%;
    background: var(--brand);
  }
</style>
</head>
<body>
<main class="menu-page">
  <section class="menu-panel">
    <h2 class="section-title combos-title">Sandwhich Combos</h2>
    <ul class="item-list combo-list">
      <li>One Side with any Sandwhich &nbsp; $X.XXX</li>
      <li>Two Sides with and Snadwhich &nbsp;$ X.xxxx</li>
      <li>Gorumet</li>
      <li>Two Sides and A Fresh Baked Cookie $ X.ooo</li>
    </ul>

    <h2 class="section-title addons-title">Sandwich Add Ons</h2>
    <ul class="item-list addon-list">
      <li>Chips</li>
      <li>Pretzels</li>
      <li>Cookies</li>
      <li>Brownie</li>
      <li>Blondie</li>
      <li>Whole Fruit</li>
      <li>Gourmet Pasta Vegetable Salad</li>
      <li>Fresh Fruit Cups</li>
      <li>Redskin Potato Salad</li>
      <li>Sesame Noodle Salad</li>
      <li>Couscous Salad</li>
      <li>Caesar Salad</li>
      <li>Tropical Salad</li>
      <li>Farm Fresh Garden Salad</li>
      <li>Country Cole Slaw</li>
    </ul>
  </section>

  <div class="food-photo" role="img" aria-label="Photograph of herb-seasoned roasted potato slices with green beans, a lemon wedge, rosemary sprig and shrimp on a white plate"></div>

  <div class="brand-mark">
    <span class="brand-dot"></span>
    <span class="brand-name">Chesapeake Valley Caterers</span>
  </div>
</main>
</body>
</html>
```